Business Card for Dental Surgery

Professional and vibrant business card for dental surgery

Other side to incorporate space for appointment date and times

My website is www.larkwooddental.com.au

Target Market(s)

All

Industry/Entity Type

Dental

Requirements
Must have
• Catchy
Phone no, internet etc
Nice to have
• portray same image as website.
on reverse appointment side:
"Please give 24 hours notice if you cannot attend"
Nice colours

```html
<!DOCTYPE html>
<html lang="en">
<head>
<meta charset="utf-8">
<title>Larkwood Dental – Business Card</title>
<link rel="stylesheet" href="https://fonts.googleapis.com/css2?family=Open+Sans:wght@400&display=swap">
<style>
  :root {
    --plum: #a45ca3;
    --leaf: #a9cd6b;
    --slate: #7d7e82;
    --paper: #ffffff;
    --ink-light: #ffffff;
  }
  html, body {
    margin: 0;
    padding: 0;
    overflow: hidden;
    background: var(--paper);
  }
  .card {
    position: relative;
    width: 1200px;
    height: 686px;
    overflow: hidden;
    background: var(--paper);
    font-family: "Open Sans", Arial, sans-serif;
  }
  .brand {
    position: absolute;
    left: 28px;
    top: 36px;
    display: flex;
    align-items: center;
    gap: 22px;
  }
  .brand-mark {
    width: 64px;
    height: 64px;
    border-radius: 50%;
    background: var(--plum);
    flex: none;
  }
  .brand-name {
    margin: 0;
    font-size: 96px;
    font-weight: 400;
    line-height: 1.1;
    color: var(--plum);
    white-space: nowrap;
  }
  .practitioners {
    position: absolute;
    left: 749px;
    top: 206px;
    margin: 0;
    padding: 0;
    list-style: none;
    color: var(--slate);
    font-size: 34px;
    letter-spacing: 1.5px;
    line-height: 43px;
  }
  .practitioners .quals {
    font-size: 16px;
    letter-spacing: 0.5px;
    margin-left: 10px;
  }
  .wave {
    position: absolute;
    left: 0;
    top: 350px;
    width: 1200px;
    height: 336px;
  }
  .contact {
    position: absolute;
    top: 462px;
    margin: 0;
    color: var(--ink-light);
    letter-spacing: 1.2px;
    font-style: normal;
  }
  .contact p {
    margin: 0;
    font-size: 31px;
    line-height: 55px;
  }
  .contact .practice-name {
    font-size: 41px;
    letter-spacing: 1.5px;
  }
  .contact-address { left: 80px; }
  .contact-lines { left: 586px; }
</style>
</head>
<body>
  <main class="card">
    <header class="brand">
      <span class="brand-mark" aria-hidden="true"></span>
      <h1 class="brand-name">Larkwood Dental</h1>
    </header>

    <ul class="practitioners">
      <li>Dr. Martin Hale<span class="quals">BDS</span></li>
      <li>Dr. Owen Clarke<span class="quals">BDS FRACDS</span></li>
    </ul>

    <svg class="wave" viewBox="0 0 1200 336" preserveAspectRatio="none" aria-hidden="true">
      <path d="M0 79 C 90 50, 160 38, 260 40 C 420 44, 560 64, 700 62 C 880 58, 1040 28, 1200 16 L1200 336 L0 336 Z" fill="var(--leaf)"/>
      <path d="M0 79 C 90 50, 160 38, 260 40 C 420 44, 560 64, 700 62 C 880 58, 1040 28, 1200 16" fill="none" stroke="var(--plum)" stroke-width="7"/>
    </svg>

    <address class="contact contact-address">
      <p class="practice-name">Larkwood Dental</p>
      <p>18 Larkwood St.</p>
      <p>Larkwood. NSW 2199</p>
    </address>

    <address class="contact contact-lines">
      <p>Phone: 02 9555 0142</p>
      <p>admin@larkwooddental.com.au</p>
      <p>www.larkwooddental.com.au</p>
    </address>
  </main>
</body>
</html>
```